Cozy Cradle Loops Needs a Beautiful Website

I need a new website for this new E-commerce. I sell handmade baby crochets, e.g. booties, headbands, hats, etc. I need a feminine and soft design to make the moms-to-be say 'oohh ahh'. I'd like pink, blue and gray. I'd like an inviting homepage, and nice regular pages where people can see and order the products.

Industry/Entity Type

Baby

Requirements
Must have
• beautiful, soft, feminine design. Please use pictures of the colors I'd like: brown, yellow, pink and blue. Any combination, but definitely include brown.

```html
<!DOCTYPE html>
<html lang="en">
<head>
<meta charset="utf-8">
<title>Cozy Cradle Loops</title>
<link rel="stylesheet" href="https://fonts.googleapis.com/css2?family=Open+Sans:wght@400;600;700;800&display=swap">
<style>
:root{
  --pink:#ec4b8c;
  --pink-soft:#f7a8c8;
  --pink-pale:#fde3ee;
  --blue:#2eb5e3;
  --blue-dark:#1b93c4;
  --sky:#dff1fa;
  --sky-deep:#c4e6f5;
  --green:#7cc142;
  --gray:#6b6f73;
  --gray-light:#e6e9eb;
  --white:#ffffff;
  --red:#e8343a;
}
*{box-sizing:border-box;margin:0;padding:0}
html,body{width:824px;height:1200px;overflow:hidden}
body{font-family:"Open Sans",Arial,sans-serif;color:var(--gray);
  background:linear-gradient(180deg,#eef8fd 0%,var(--sky) 60%,var(--sky-deep) 100%);position:relative}
.page{position:absolute;left:67px;top:0;width:690px;height:1200px}
/* header */
.brand{position:absolute;left:0;top:18px;display:flex;align-items:center;gap:8px}
.brand-dot{width:22px;height:22px;border-radius:50%;background:var(--pink-soft)}
.brand-name{font-weight:800;font-size:25px;color:var(--pink);letter-spacing:-.3px}
.top-links{position:absolute;right:0;top:8px;display:flex;gap:14px;font-size:9px;color:var(--gray)}
.search{position:absolute;right:0;top:40px;display:flex}
.search input{width:120px;height:22px;border:1px solid var(--pink-soft);border-right:0;font:9px "Open Sans",sans-serif;padding:0 6px;color:var(--gray)}
.search button{width:26px;height:22px;border:0;background:var(--pink);display:flex;align-items:center;justify-content:center}
.nav{position:absolute;left:0;top:88px;width:690px;height:28px;background:var(--pink);border-radius:3px;display:flex;justify-content:space-around;align-items:center}
.nav a{color:var(--white);font-size:10px;font-weight:600;text-decoration:none}
/* hero */
.hero{position:absolute;left:0;top:130px;width:690px;height:265px}
.hero-main{position:absolute;left:0;top:0;width:540px;height:265px;border:4px solid var(--white);
  background:linear-gradient(120deg,#f9d3e2 0%,#f4b7cd 45%,#e9c7b4 100%);box-shadow:0 1px 4px rgba(0,0,0,.12)}
.hero-sale{position:absolute;left:40px;top:130px;font-size:38px;font-weight:800;color:var(--pink)}
.dots{position:absolute;right:12px;bottom:10px;display:flex;gap:4px}
.dots span{width:7px;height:7px;border-radius:50%;background:var(--white)}
.dots span.on{background:var(--pink)}
.side{position:absolute;left:552px;width:138px;height:125px;background:var(--white);border:4px solid var(--white);box-shadow:0 1px 4px rgba(0,0,0,.12)}
.side.a{top:0}.side.b{top:140px}
.side-text{position:absolute;left:6px;top:8px;width:66px}
.side-text b{display:block;color:var(--pink);font-size:15px;font-weight:800}
.side-text small{font-size:7px;line-height:1.25;display:block}
.side-art{position:absolute;right:4px;bottom:8px;width:62px;height:62px;border-radius:6px}
.side.a .side-art{background:linear-gradient(135deg,#f7c3d8,#ec89b0)}
.side.b .side-art{background:linear-gradient(135deg,#c8c1bb,#5b4a44)}
/* sections */
.section-title{position:absolute;left:0;width:690px;display:flex;align-items:center;gap:10px;color:var(--pink);font-size:17px;font-weight:700}
.section-title::after{content:"";flex:1;height:2px;background:var(--sky-deep)}
.grid{position:absolute;left:0;width:690px;display:grid;grid-template-columns:repeat(5,1fr);gap:15px}
.card{background:var(--white);border:1px solid var(--gray-light);height:200px;position:relative;overflow:hidden}
.card-art{height:118px;margin:6px;border-radius:3px}
.ribbon{position:absolute;right:-20px;top:8px;width:70px;transform:rotate(45deg);background:var(--red);color:var(--white);font-size:7px;font-weight:700;text-align:center;line-height:13px}
.card-name{text-align:center;font-size:11px;color:var(--gray);margin-top:10px}
.card-bar{position:absolute;left:0;right:0;bottom:0;height:26px;background:var(--blue);display:flex;justify-content:space-between;align-items:center;padding:0 8px;color:var(--white);font-size:9px;font-weight:600}
.card-bar span+span{font-weight:400}
/* info boxes */
.boxes{position:absolute;left:0;top:905px;width:690px;height:75px;display:grid;grid-template-columns:repeat(4,1fr);gap:8px}
.box{padding:8px 10px;color:var(--white)}
.box h4{font-size:11px;font-weight:700;margin-bottom:6px}
.box.news{background:var(--green)}
.box.social{background:var(--pink)}
.box.ship{background:var(--blue)}
.box.back{background:var(--pink)}
.news-field{display:flex}
.news-field span{flex:1;background:var(--white);height:18px;font-size:7px;color:#9aa;padding:4px}
.news-field b{width:22px;background:#5a9a2c}
.circles{display:flex;gap:6px;margin-top:4px}
.circles i{width:20px;height:20px;border-radius:50%;background:var(--white);opacity:.9}
.box small{font-size:7px;display:block;margin-top:-3px}
.big{font-size:15px;font-weight:700;margin-top:6px;display:flex;align-items:center;gap:6px}
/* footer */
.footer-art{position:absolute;left:0;top:990px;width:824px;height:210px;
  background:linear-gradient(180deg,rgba(255,255,255,0) 0%,#cfead7 70%,#a9d98a 100%)}
.footer{position:absolute;left:0;top:1005px;width:690px;display:grid;grid-template-columns:1.2fr 1fr 1.2fr 1fr 1fr;gap:10px;font-size:8px}
.footer h5{font-size:9px;font-weight:700;color:var(--gray);margin-bottom:6px;letter-spacing:.3px}
.footer li{list-style:none;line-height:14px}
.copy{position:absolute;left:0;top:1180px;width:690px;text-align:center;font-size:7px;color:var(--gray)}
</style>
</head>
<body>
<div class="footer-art" role="img" aria-label="Soft garden scene with grass, flowers and round trees"></div>
<div class="page">
  <header>
    <div class="brand"><span class="brand-dot"></span><span class="brand-name">Cozy Cradle Loops</span></div>
    <div class="top-links"><span>Wish List (0)</span><span>My Account</span><span>Shopping Cart</span><span>Checkout</span></div>
    <div class="search"><input value="Search"><button aria-label="Search">
      <svg width="11" height="11" viewBox="0 0 12 12"><circle cx="5" cy="5" r="3.6" fill="none" stroke="#fff" stroke-width="1.6"/><line x1="7.6" y1="7.6" x2="11" y2="11" stroke="#fff" stroke-width="1.6"/></svg></button></div>
    <nav class="nav"><a>Home</a><a>About Us</a><a>Booties</a><a>Headbands</a><a>Hats</a><a>Blog</a><a>Contact Us</a></nav>
  </header>

  <section class="hero">
    <div class="hero-main" role="img" aria-label="Sleeping newborn wearing a pink crochet headband on a soft pink blanket">
      <div class="hero-sale">SALE 50%</div>
      <div class="dots"><span class="on"></span><span></span><span></span></div>
    </div>
    <div class="side a"><div class="side-text"><b>SALE 50%</b><small>soft handmade knits for little ones</small></div><div class="side-art" role="img" aria-label="Pink crochet crown"></div></div>
    <div class="side b"><div class="side-text"><b>SALE 50%</b><small>cozy booties for tiny feet today</small></div><div class="side-art" role="img" aria-label="Brown polka dot baby shoes"></div></div>
  </section>

  <h2 class="section-title" style="top:410px">Latest</h2>
  <div class="grid" style="top:438px">
    <div class="card"><div class="ribbon">NEW</div><div class="card-art" role="img" aria-label="Pink crochet crown" style="background:linear-gradient(135deg,#fbd3e3,#f07aa8)"></div><p class="card-name">Crown</p><div class="card-bar"><span>$65.75</span><span>Add to Cart</span></div></div>
    <div class="card"><div class="ribbon">NEW</div><div class="card-art" role="img" aria-label="Pink and brown crochet shoes" style="background:linear-gradient(135deg,#f3d6d8,#a06a5c)"></div><p class="card-name">Shoes</p><div class="card-bar"><span>$65.75</span><span>Add to Cart</span></div></div>
    <div class="card"><div class="ribbon">NEW</div><div class="card-art" role="img" aria-label="Beige crochet sun hat" style="background:linear-gradient(135deg,#f4e6d2,#c9a57f)"></div><p class="card-name">Hats</p><div class="card-bar"><span>$65.75</span><span>Add to Cart</span></div></div>
    <div class="card"><div class="ribbon">NEW</div><div class="card-art" role="img" aria-label="Pink crochet booties" style="background:linear-gradient(135deg,#fde2ec,#f49bbd)"></div><p class="card-name">Booties</p><div class="card-bar"><span>$65.75</span><span>Add to Cart</span></div></div>
    <div class="card"><div class="ribbon">NEW</div><div class="card-art" role="img" aria-label="Pink flower crochet booties" style="background:linear-gradient(135deg,#fbe0ea,#e77aa5)"></div><p class="card-name">Booties</p><div class="card-bar"><span>$65.75</span><span>Add to Cart</span></div></div>
  </div>

  <h2 class="section-title" style="top:660px">Specials</h2>
  <div class="grid" style="top:688px">
    <div class="card"><div class="ribbon">NEW</div><div class="card-art" role="img" aria-label="Navy crochet sneakers" style="background:linear-gradient(135deg,#d8e3ee,#2f4a6e)"></div><p class="card-name">Crown</p><div class="card-bar"><span>$65.75</span><span>Add to Cart</span></div></div>
    <div class="card"><div class="ribbon">NEW</div><div class="card-art" role="img" aria-label="Aqua crochet crown" style="background:linear-gradient(135deg,#d5f1f3,#5cc7cf)"></div><p class="card-name">Shoes</p><div class="card-bar"><span>$65.75</span><span>Add to Cart</span></div></div>
    <div class="card"><div class="ribbon">NEW</div><div class="card-art" role="img" aria-label="Crochet beanie with flower" style="background:linear-gradient(135deg,#e7efe0,#9fb98a)"></div><p class="card-name">Hats</p><div class="card-bar"><span>$65.75</span><span>Add to Cart</span></div></div>
    <div class="card"><div class="ribbon">NEW</div><div class="card-art" role="img" aria-label="Turquoise crochet booties" style="background:linear-gradient(135deg,#d9f0ee,#3fa9a6)"></div><p class="card-name">Booties</p><div class="card-bar"><span>$65.75</span><span>Add to Cart</span></div></div>
    <div class="card"><div class="ribbon">NEW</div><div class="card-art" role="img" aria-label="Pink and blue crochet booties" style="background:linear-gradient(135deg,#e3ecf7,#e98fb4)"></div><p class="card-name">Booties</p><div class="card-bar"><span>$65.75</span><span>Add to Cart</span></div></div>
  </div>

  <div class="boxes">
    <div class="box news"><h4>Newsletter</h4><div class="news-field"><span>Enter your email</span><b></b></div></div>
    <div class="box social"><h4>Social Network</h4><div class="circles"><i></i><i></i><i></i><i></i></div></div>
    <div class="box ship"><h4>Free Delivery</h4><small>on every local order</small>
      <div class="big"><svg width="16" height="12" viewBox="0 0 16 12"><rect x="0" y="1" width="10" height="7" fill="#fff"/><path d="M10 3h3l3 3v2h-6z" fill="#fff"/><circle cx="3.5" cy="10" r="1.8" fill="#fff"/><circle cx="12.5" cy="10" r="1.8" fill="#fff"/></svg>Oder over $30</div></div>
    <div class="box back"><h4>Return Money</h4><small>easy and quick refund</small>
      <div class="big"><svg width="14" height="14" viewBox="0 0 14 14"><circle cx="7" cy="7" r="6" fill="none" stroke="#fff" stroke-width="1.6"/><path d="M4 7l2 2 4-4" fill="none" stroke="#fff" stroke-width="1.6"/></svg>7 days return</div></div>
  </div>

  <footer class="footer">
    <div><h5>SUPPORT</h5><ul><li>(+01) 555 201 190</li><li>(+01) 555 201 191</li><li>hello@cozycradle.example</li></ul></div>
    <div><h5>INFORMATION</h5><ul><li>Specials</li><li>New products</li><li>Best sellers</li><li>Our stores</li><li>Contact us</li><li>Sitemap</li></ul></div>
    <div><h5>CUSTOMER SERVICE</h5><ul><li>Delivery</li><li>Legal Notice</li><li>Terms and conditions of use</li><li>About us</li><li>Secure payment</li></ul></div>
    <div><h5>MY ACCOUNT</h5><ul><li>My orders</li><li>My credit slips</li><li>My addresses</li><li>My personal info</li><li>My vouchers</li></ul></div>
    <div><h5>EXTRAS</h5><ul><li>Brands</li><li>Gift vouchers</li><li>Affiliates</li><li>Specials</li></ul></div>
  </footer>
  <p class="copy">© 2014 Cozy Cradle Loops. All Rights Reserved.</p>
</div>
</body>
</html>
```